Business card por a urban DJ, up scale audience target

Need a sober design, modern, conservative colors but i can consider some options, y play rnb, hip hop, EDM and top40.

Business card for contact and personal info, double sided, use logo attrached please; im 42 so i need a card acording to my age an target audience.

Target Market(s)

Adult people, up scale audience

Industry/Entity Type

Music Download

Contact Information for Business Card

Cel (318) 4207265518 www.lumadrift.com

Requirements
Must have
• open mind
Nice to have
• open mind
Should not have
• DJ

```html
<!DOCTYPE html>
<html lang="en">
<head>
<meta charset="utf-8">
<title>LUMA – Business Card</title>
<link rel="stylesheet" href="https://fonts.googleapis.com/css2?family=Open+Sans:wght@400;700;800&display=swap">
<style>
  :root {
    --page: #e9e7e3;
    --card-white: #ffffff;
    --card-black: #1d1d1d;
    --ink: #2a2a2a;
    --ink-soft: #4a4a4a;
    --band-grey: #333333;
    --band-black: #0c0c0c;
    --mark-grey: #6e6e6e;
  }
  * { margin: 0; padding: 0; box-sizing: border-box; }
  html, body {
    width: 1200px; height: 900px; overflow: hidden;
    background: var(--page);
    font-family: "Open Sans", Arial, sans-serif;
  }
  .canvas {
    position: relative; width: 1200px; height: 900px;
    display: flex; flex-direction: column; align-items: center; justify-content: center; gap: 48px;
  }
  .card {
    position: relative; width: 660px; height: 377px; overflow: hidden;
    box-shadow: 0 6px 18px rgba(0,0,0,.18);
  }
  /* Back side */
  .card--back { background: var(--card-black); }
  .card--back .wordmark {
    position: absolute; left: 50%; top: 50%; transform: translate(-50%, -50%);
    color: var(--mark-grey);
    font-size: 150px; font-weight: 800; line-height: 1; letter-spacing: 4px;
  }

  /* Front side */
  .card--front { background: var(--card-white); color: var(--ink); }
  .card__bands { position: absolute; inset: 0; width: 100%; height: 100%; }
  .band--grey { fill: var(--band-grey); }
  .band--black { fill: var(--band-black); }
  .identity { position: absolute; left: 60px; top: 26px; }
  .identity__name { font-size: 21px; font-weight: 700; line-height: 1.1; }
  .identity__title { font-size: 13px; color: var(--ink-soft); }
  .contact { position: absolute; left: 28px; top: 138px; font-size: 15px; line-height: 1.2; font-style: normal; }
  .contact__address { margin-bottom: 10px; }
  .contact__row { display: flex; align-items: center; gap: 7px; }
  .contact__icon { width: 11px; height: 11px; fill: var(--ink); flex: none; }
  .card--front .wordmark {
    position: absolute; right: 56px; top: 126px;
    color: var(--ink);
    font-size: 108px; font-weight: 800; line-height: 1; letter-spacing: 3px;
  }
</style>
</head>
<body>
<main class="canvas">
  <section class="card card--back" aria-label="Card back">
    <p class="wordmark">LUMA</p>
  </section>

  <section class="card card--front" aria-label="Card front">
    <svg class="card__bands" viewBox="0 0 660 377" preserveAspectRatio="none" aria-hidden="true">
      <polygon class="band--grey" points="0,0 40,0 28,18 0,18"/>
      <polygon class="band--grey" points="22,44 46,12 46,44"/>
      <polygon class="band--grey" points="0,300 0,322 285,322 296,300"/>
      <polygon class="band--black" points="306,304 660,304 660,377 0,377 0,345 288,345"/>
    </svg>

    <div class="identity">
      <p class="identity__name">Marco Reyes</p>
      <p class="identity__title">Managing Director</p>
    </div>

    <address class="contact">
      <p class="contact__address">12345, Address Goes Here<br>Country Name, 123456</p>
      <p class="contact__row">
        <svg class="contact__icon" viewBox="0 0 24 24"><path d="M6.6 10.8a15 15 0 0 0 6.6 6.6l2.2-2.2a1 1 0 0 1 1-.25 11.4 11.4 0 0 0 3.6.57 1 1 0 0 1 1 1V20a1 1 0 0 1-1 1A17 17 0 0 1 3 4a1 1 0 0 1 1-1h3.5a1 1 0 0 1 1 1c0 1.25.2 2.45.57 3.57a1 1 0 0 1-.25 1z"/></svg>
        (318) 4207265518
      </p>
      <p class="contact__row">
        <svg class="contact__icon" viewBox="0 0 24 24"><circle cx="12" cy="12" r="10" fill="none" stroke="#2a2a2a" stroke-width="3"/><path d="M2 12h20M12 2c3 3 3 17 0 20M12 2c-3 3-3 17 0 20" fill="none" stroke="#2a2a2a" stroke-width="2"/></svg>
        www.lumadrift.com
      </p>
      <p class="contact__row">
        <svg class="contact__icon" viewBox="0 0 24 24"><path d="M2 5h20v14H2z"/><path d="M2 5l10 8 10-8" fill="none" stroke="#fff" stroke-width="2"/></svg>
        info@lumadrift.com
      </p>
    </address>

    <p class="wordmark">LUMA</p>
  </section>
</main>
</body>
</html>
```